Design a New Business Card for Our Company

We are looking for fresh, unique, and a modern business card that reflects our roots as digital marketing agency focused on SEM.

Industry/Entity Type

Marketing

Contact Information for Business Card

looking for very unique out of the box designs. clean and modern that compliments our logo

Requirements
Must have
• colors should match our logo
• Front should have name, address, email, and phone/fax of the person, phone/fax are the same number
• back should have our url

```html
<!DOCTYPE html>
<html lang="en">
<head>
<meta charset="utf-8">
<title>Brightpath Media – Business Card</title>
<link rel="stylesheet" href="https://fonts.googleapis.com/css2?family=Arimo:ital,wght@0,400;0,700;1,400&display=swap">
<style>
  :root {
    --brand-blue: #1b5fa4;
    --band-grey: #a9b3bd;
    --accent-blue: #4a9fd8;
    --mark-grey: #a7abb0;
    --faint-blue: #dce7f3;
    --paper: #ffffff;
    --backdrop: #f3f3f3;
    --ink: #222222;
  }
  html, body {
    margin: 0;
    padding: 0;
    width: 904px;
    height: 1200px;
    overflow: hidden;
    background: var(--backdrop);
    font-family: "Arimo", Arial, sans-serif;
  }
  .canvas {
    position: relative;
    width: 904px;
    height: 1200px;
  }
  .side-label {
    position: absolute;
    margin: 0;
    font-size: 34px;
    font-weight: 400;
    color: var(--ink);
  }
  .side-label--front { left: 776px; top: 28px; }
  .side-label--back { left: 32px; top: 628px; }
  .card {
    position: absolute;
    width: 427px;
    height: 260px;
    background: var(--paper);
    box-shadow: 0 2px 8px rgba(0,0,0,0.12);
  }
  .card--front { left: 143px; top: 137px; }
  .card--back { left: 334px; top: 746px; }
  .card svg { display: block; width: 100%; height: 100%; }
  .fill-blue { fill: var(--brand-blue); }
  .fill-grey { fill: var(--band-grey); }
  .fill-paper { fill: var(--paper); }
  .brand-dot { fill: var(--accent-blue); }
  .brand-name { fill: var(--mark-grey); font-weight: 700; font-size: 25px; }
  .holder-name { fill: var(--brand-blue); font-weight: 700; font-size: 12px; }
  .holder-title { fill: var(--ink); font-style: italic; font-size: 11px; }
  .address { fill: var(--paper); font-size: 9.5px; }
  .contact { fill: var(--ink); font-size: 9.5px; }
  .contact-key { fill: var(--brand-blue); font-weight: 700; }
  .brand-faint { fill: var(--faint-blue); font-weight: 700; font-size: 34px; }
  .web-address { fill: var(--paper); font-size: 9.5px; }
</style>
</head>
<body>
<main class="canvas">
  <h2 class="side-label side-label--front">Front</h2>
  <section class="card card--front" aria-label="Business card front">
    <svg viewBox="0 0 530 323" xmlns="http://www.w3.org/2000/svg">
      <rect class="fill-blue" x="0" y="0" width="530" height="20"/>
      <polygon class="fill-grey" points="0,23 228,23 238,45 0,45"/>
      <polygon class="fill-blue" points="230,23 530,23 530,82 257,82"/>
      <circle class="brand-dot" cx="278" cy="130" r="12"/>
      <text class="brand-name" x="298" y="139">Brightpath Media</text>
      <text class="holder-name" x="17" y="211">My Name</text>
      <text class="holder-title" x="17" y="226">Designation</text>
      <polygon class="fill-blue" points="0,241 196,241 216,298 0,298"/>
      <polygon class="fill-grey" points="211,278 530,278 530,298 218,298"/>
      <text class="address" x="23" y="267">418 Alder Grove Rd Fairmont,</text>
      <text class="address" x="23" y="280">OR 97455 USA</text>
      <text class="contact" x="222" y="271"><tspan class="contact-key">p</tspan> 555-201-4470 <tspan class="contact-key" dx="6">f</tspan> 555-201-4470 <tspan class="contact-key" dx="6">e</tspan> hello@brightpathmedia.com</text>
      <rect class="fill-blue" x="0" y="303" width="530" height="20"/>
    </svg>
  </section>

  <h2 class="side-label side-label--back">Back</h2>
  <section class="card card--back" aria-label="Business card back">
    <svg viewBox="0 0 530 323" xmlns="http://www.w3.org/2000/svg">
      <rect class="fill-blue" x="0" y="0" width="530" height="22"/>
      <text class="brand-faint" x="265" y="152" text-anchor="middle">Brightpath Media</text>
      <rect class="fill-grey" x="0" y="277" width="530" height="20"/>
      <polygon class="fill-blue" points="137,265 388,265 417,299 112,299"/>
      <text class="web-address" x="265" y="286" text-anchor="middle">www.brightpathmedia.com</text>
      <rect class="fill-blue" x="0" y="301" width="530" height="22"/>
    </svg>
  </section>
</main>
</body>
</html>
```